Executive Business Card for Healthcare Company [Need Today]

I need a business card design for a healthcare company. The only branding the company has thus far is a logo. The cards will be utilized by company executives. The design I envision will be vibrant and appealing but with a corporate feel. They shouldn't be too casual or playful. I would like to complete this project TODAY if possible.

Target Market(s)

Healthcare vendors, other executives in healthcare and pharmaceuticals

Industry/Entity Type

Pharmaceutical

Contact Information for Business Card

See attachment

Font styles to use
Serif
Sans Serif

Colors

Designer to choose colors to be used in the design.

```html
<!DOCTYPE html>
<html lang="en">
<head>
<meta charset="utf-8">
<title>Corvane Therapeutics – Business Card</title>
<link href="https://fonts.googleapis.com/css2?family=Roboto:wght@300;400&display=swap" rel="stylesheet">
<style>
  :root{
    --backdrop:#3a3a3c;
    --card:#232325;
    --teal:#1fb3c4;
    --green:#3dbf94;
    --ink-light:#e9ecec;
    --ink-soft:#b9c0c2;
  }
  *{margin:0;padding:0;box-sizing:border-box}
  html,body{width:799px;height:1200px;overflow:hidden}
  body{background:var(--backdrop);font-family:"Roboto",Arial,sans-serif;position:relative}
  .card{position:absolute;left:70px;width:660px;height:377px;background:var(--card);border-radius:4px;overflow:hidden;box-shadow:0 6px 18px rgba(0,0,0,.35)}
  .card--front{top:150px}
  .card--back{top:675px}

  /* front */
  .front-lockup{position:absolute;left:120px;top:120px;display:flex;align-items:center;gap:26px}
  .brand-dot{width:104px;height:104px;border:4px solid var(--green);border-radius:50%;flex:none}
  .brand-name{color:var(--teal);font-weight:300;font-size:46px;line-height:1.05;letter-spacing:.5px}
  .website{position:absolute;left:0;right:0;top:292px;text-align:center;color:var(--ink-soft);font-size:15px;letter-spacing:4px;font-weight:300}

  /* back */
  .back-band{position:absolute;inset:0}
  .back-name{position:absolute;left:34px;top:20px;color:var(--teal);font-weight:300;font-size:32px;line-height:1.05}
  .contact{position:absolute;left:34px;top:118px;color:var(--ink-light)}
  .contact__name{font-size:26px;font-weight:400}
  .contact__title{font-size:13px;font-weight:300;margin:2px 0 10px;color:#eefaf8}
  .contact__list{list-style:none;font-size:15px;font-weight:300;line-height:1.45}
  .contact__list li{display:flex;align-items:center;gap:8px}
  .contact__list svg{width:12px;height:12px;fill:var(--ink-light)}
  .address{position:absolute;left:34px;top:324px;color:var(--ink-light);font-size:15px;font-weight:300}
</style>
</head>
<body>

<section class="card card--front">
  <div class="front-lockup">
    <span class="brand-dot"></span>
    <div class="brand-name">Corvane<br>Therapeutics</div>
  </div>
  <p class="website">www.corvanerx.com</p>
</section>

<section class="card card--back">
  <svg class="back-band" viewBox="0 0 660 377" width="660" height="377">
    <defs>
      <linearGradient id="bandFill" x1="0" y1="0" x2="0.4" y2="1">
        <stop offset="0" stop-color="#1fb3c4"/>
        <stop offset="1" stop-color="#3dbf94"/>
      </linearGradient>
    </defs>
    <polygon points="0,100 500,100 540,145 660,145 660,300 0,300" fill="url(#bandFill)"/>
    <circle cx="505" cy="230" r="104" fill="#232325"/>
    <circle cx="505" cy="230" r="88" fill="none" stroke="#3dbf94" stroke-width="4"/>
  </svg>
  <div class="back-name">Corvane<br>Therapeutics</div>
  <div class="contact">
    <h1 class="contact__name">Daniel Hartley</h1>
    <p class="contact__title">Senior Director of Marketing</p>
    <ul class="contact__list">
      <li><svg viewBox="0 0 12 12"><path d="M2 1h3l1 3-2 1a7 7 0 0 0 3 3l1-2 3 1v3c-6 1-10-3-9-9z"/></svg>555-210-4837</li>
      <li><svg viewBox="0 0 12 12"><rect x="3" y="0.5" width="6" height="11" rx="1"/></svg>555-398-1562</li>
      <li><svg viewBox="0 0 12 12"><circle cx="6" cy="6" r="5.5"/></svg>dhartley@corvanerx.com</li>
    </ul>
  </div>
  <p class="address">118 Linden Avenue Marlow, GA 30990</p>
</section>

</body>
</html>
```